project - Misto Den

Dear designers, I'm Looking for an appealing new business card design to represent us for our new e-cigarette store: The Misto Den. Knowledgeable and friendly staff we aim for superior customer service with a positive atmosphere. Classic feel with modern touch is what we are aiming for . Lime green font and grey back round is the original color scheme but we are flexible and open to suggestions. I added some doodles to show you where my mind is at. address: 4827 203 St SW Edmonton, AB (inside the grand swap bazaar)web: themistoden.com email: info@themistoden.com phone : 555.214.6093 Thanks and am looking forward to seeing your creative , fresh and innovative designs.
Good luck everybody!
Gordon
Updates
lime green and charcoal grey please. thanks
Industry/Entity Type
Business
Logo Text
The Misto Den
Look and feel
Each slider illustrates characteristics of the customer's brand and the style your logo design should communicate.

```html
<!DOCTYPE html>
<html lang="en">
<head>
<meta charset="utf-8">
<title>The Misto Den – Business Card</title>
<link rel="stylesheet" href="https://fonts.googleapis.com/css2?family=Quicksand:wght@400;600&display=swap">
<style>
  :root {
    --page-bg: #ffffff;
    --card-charcoal: #252d2e;
    --lime: #b5f21a;
    --divider-grey: #7b8080;
    --tagline-grey: #9a9c9c;
  }
  html, body {
    margin: 0;
    padding: 0;
    width: 1200px;
    height: 1000px;
    overflow: hidden;
    background: var(--page-bg);
  }
  .canvas {
    position: relative;
    width: 1200px;
    height: 1000px;
  }
  .card {
    position: absolute;
    left: 57px;
    top: 181px;
    width: 1086px;
    height: 638px;
    background: var(--card-charcoal);
  }
  .divider {
    position: absolute;
    left: 459px;
    top: 335px;
    width: 4px;
    height: 242px;
    background: var(--divider-grey);
  }
  .brand {
    position: absolute;
    right: 113px;
    top: 441px;
    text-align: right;
    font-family: "Quicksand", sans-serif;
  }
  .brand-name {
    margin: 0;
    font-weight: 600;
    font-size: 75px;
    line-height: 1;
    letter-spacing: -1px;
    color: var(--lime);
    white-space: nowrap;
  }
  .brand-tagline {
    margin: 16px 0 0;
    font-weight: 400;
    font-size: 44px;
    line-height: 1;
    letter-spacing: 0.5px;
    color: var(--tagline-grey);
    white-space: nowrap;
  }
</style>
</head>
<body>
  <div class="canvas">
    <section class="card" aria-label="Business card front">
      <div class="divider"></div>
      <div class="brand">
        <h1 class="brand-name">The Misto Den</h1>
        <p class="brand-tagline">e-cigarette store</p>
      </div>
    </section>
  </div>
</body>
</html>
```